Dynamic Business Card for Sports Supplements Company

Hi! I'm looking for an awesome business card to match my existing sports supplement company. I have uploaded my current company logo and screenshot of the front page of my website.

I would like to have something dynamic and interesting and utilize the colors in the website - the reds and purples

The business card should be double sided and focus on a unique eye-catching design on the back and include all the relevant company info.

Most importantly, it should say somewhere: "Sign up on our website for a coupon code."

Target Market(s)

Mostly for women gym goers but it shouldn't be too feminine. It should be in keeping with the website design. It should flow and clearly be connected to it

Industry/Entity Type

Business

Contact Information for Business Card

Lorraine K. Vestal
CEO
LVestal@Quorvanexco.com
www.quorvanexco.com
555.417.3820
P.O. Box 47315
Marlow, Oregon 00000

Sign up on our website for a coupon code

Font styles to use
Serif
Sans Serif
Other font styles liked:
• Novecento font family and "Quorvanex" is in AR Destine font

Requirements
Must have
• One side should be a bold Quorvanex logo design. Even just the symbol itself may be o.k. (see attached file)

```html
<!DOCTYPE html>
<html lang="en">
<head>
<meta charset="utf-8">
<title>Quorvanex Business Card</title>
<link href="https://fonts.googleapis.com/css2?family=Arimo:wght@400;700&display=swap" rel="stylesheet">
<style>
  :root {
    --backdrop: #3b3431;
    --card: #141414;
    --card-edge: #1f1f1f;
    --red: #d7262b;
    --white: #f4f4f4;
    --grey: #8a8a8a;
    --soft-grey: #b9b9b9;
  }
  * { box-sizing: border-box; margin: 0; padding: 0; }
  html, body { width: 1200px; height: 864px; overflow: hidden; }
  body {
    background: var(--backdrop);
    font-family: "Arimo", Arial, sans-serif;
    position: relative;
  }
  .card {
    position: absolute;
    width: 560px;
    height: 320px;
    background: var(--card);
    border: 1px solid var(--card-edge);
    border-radius: 4px;
    box-shadow: 0 14px 30px rgba(0,0,0,0.45);
    overflow: hidden;
  }

  /* Back side */
  .card-back { left: 70px; top: 110px; }
  .back-brand {
    position: absolute;
    left: 120px; top: 88px;
    display: flex; align-items: center; gap: 14px;
  }
  .brand-square { display: block; background: var(--red); }
  .back-brand .brand-square { width: 34px; height: 34px; }
  .back-brand .brand-name {
    font-weight: 700;
    font-size: 46px;
    letter-spacing: 1px;
    color: var(--soft-grey);
    text-transform: uppercase;
  }
  .coupon-note {
    position: absolute;
    left: 50px; top: 198px;
    font-size: 13px;
    color: var(--grey);
    letter-spacing: 0.2px;
  }

  /* Front side */
  .card-front { left: 570px; top: 470px; }
  .front-brand {
    position: absolute;
    left: 0; top: 0;
    width: 290px; height: 100%;
    display: flex; flex-direction: column; align-items: center; justify-content: center;
    gap: 8px;
  }
  .front-brand .brand-row { display: flex; align-items: center; gap: 10px; }
  .front-brand .brand-square { width: 22px; height: 22px; }
  .front-brand .brand-name {
    font-weight: 700;
    font-size: 30px;
    color: var(--white);
    text-transform: uppercase;
    letter-spacing: 0.5px;
  }
  .tagline {
    font-size: 9.5px;
    letter-spacing: 2.6px;
    color: var(--grey);
    text-transform: uppercase;
  }
  .divider {
    position: absolute;
    left: 300px; top: 40px;
    width: 1px; height: 240px;
    background: linear-gradient(to bottom, transparent, #6a6a6a 20%, #6a6a6a 80%, transparent);
  }
  .contact {
    position: absolute;
    left: 322px; top: 62px;
    color: var(--white);
    font-size: 14px;
    line-height: 1.35;
  }
  .contact-name { color: var(--red); font-size: 19px; }
  .contact-role { margin-bottom: 14px; }
  .contact-address { margin-bottom: 8px; }
  .contact-line { display: flex; align-items: center; gap: 8px; margin-bottom: 3px; }
  .contact-line svg { width: 14px; height: 14px; flex: none; }
</style>
</head>
<body>

  <section class="card card-back" aria-label="Card back">
    <div class="back-brand">
      <span class="brand-square"></span>
      <span class="brand-name">Quorvanex</span>
    </div>
    <p class="coupon-note">Sign up on our website for a coupon code</p>
  </section>

  <section class="card card-front" aria-label="Card front">
    <div class="front-brand">
      <div class="brand-row">
        <span class="brand-square"></span>
        <span class="brand-name">Quorvanex</span>
      </div>
      <span class="tagline">Your Strength Companion</span>
    </div>
    <div class="divider"></div>
    <div class="contact">
      <p class="contact-name">Lorraine K. Vestal</p>
      <p class="contact-role">CEO</p>
      <p class="contact-address">P.O. Box 47315<br>Marlow, Oregon 00000</p>
      <p class="contact-line">
        <svg viewBox="0 0 16 16" aria-hidden="true"><path fill="#d7262b" d="M3 2h3l1.5 3.5-2 1.2a8 8 0 0 0 3.8 3.8l1.2-2L14 10v3a1 1 0 0 1-1 1A11 11 0 0 1 2 3a1 1 0 0 1 1-1z"/></svg>
        555.417.3820
      </p>
      <p class="contact-line">
        <svg viewBox="0 0 16 16" aria-hidden="true"><rect x="1" y="3" width="14" height="10" rx="1" fill="#d7262b"/><path d="M1.5 3.5 8 9l6.5-5.5" fill="none" stroke="#141414" stroke-width="1.3"/></svg>
        LVestal@Quorvanexco.com
      </p>
      <p class="contact-line">
        <svg viewBox="0 0 16 16" aria-hidden="true"><circle cx="8" cy="8" r="7" fill="#d7262b"/><path d="M1 8h14M8 1c-3 3-3 11 0 14M8 1c3 3 3 11 0 14" fill="none" stroke="#141414" stroke-width="1"/></svg>
        www.quorvanexco.com
      </p>
    </div>
  </section>

</body>
</html>
```